Business Card Design

We need a business card designed for our new company. Prefer a black card with white logo & writing.

Contact Information for Business Card

Ted Galloway, address: 7-4812 Fernhollow Road, Abbotsford, BC, V3K 8R2, Office Phone: 604-712-3390, Cell: 604-947-2164, Email: ted@resinworkshub.ca

Colors

Designer to choose only greyscale colors for use in the design.

```html
<!DOCTYPE html>
<html lang="en">
<head>
<meta charset="utf-8">
<title>Resinworks Hub – Business Card</title>
<link rel="stylesheet" href="https://fonts.googleapis.com/css2?family=Poppins:wght@300;400;700;800&display=swap">
<style>
  :root {
    --backdrop: #222224;
    --card: #1b1b1d;
    --card-edge: #2e2e31;
    --ink: #ffffff;
    --ink-soft: #d9d9d9;
    --rule: #8a8a8a;
  }
  * { margin: 0; padding: 0; box-sizing: border-box; }
  html, body {
    width: 1200px; height: 711px; overflow: hidden;
    background: var(--backdrop);
    font-family: "Poppins", sans-serif;
    color: var(--ink);
  }
  .canvas {
    position: relative; width: 1200px; height: 711px;
    display: flex; align-items: center; justify-content: center; gap: 40px;
  }
  .card {
    position: relative;
    width: 540px; height: 309px;
    background: var(--card);
    border: 1px solid var(--card-edge);
    border-radius: 4px;
    box-shadow: 0 10px 30px rgba(0,0,0,0.45);
  }
  .brand {
    font-weight: 800;
    color: var(--ink);
    text-transform: uppercase;
    line-height: 1;
    letter-spacing: 0.5px;
  }
  .card-front { display: flex; align-items: center; justify-content: center; }
  .card-front .brand { font-size: 40px; }

  .card-back .brand-area {
    position: absolute; left: 0; top: 0; width: 250px; height: 240px;
    display: flex; align-items: center; justify-content: center;
  }
  .card-back .brand { font-size: 27px; }
  .divider {
    position: absolute; left: 258px; top: 40px;
    width: 1px; height: 165px; background: var(--rule);
  }
  .contact { position: absolute; left: 292px; top: 44px; }
  .person-name { font-size: 30px; font-weight: 300; line-height: 1.05; }
  .person-name strong { font-weight: 800; }
  .person-role { font-size: 12px; font-weight: 400; color: var(--ink-soft); margin-top: 2px; }
  .contact-list { list-style: none; margin-top: 16px; }
  .contact-list li {
    display: flex; align-items: center; gap: 10px;
    font-size: 12.5px; font-weight: 300; line-height: 1; margin-bottom: 9px;
  }
  .contact-list svg { width: 13px; height: 13px; flex: none; }
  .address {
    position: absolute; left: 0; right: 0; bottom: 30px;
    text-align: center; font-size: 13px; font-weight: 400; letter-spacing: 0.2px;
  }
</style>
</head>
<body>
<main class="canvas">
  <section class="card card-front" aria-label="Card front">
    <div class="brand">Resinworks Hub</div>
  </section>

  <section class="card card-back" aria-label="Card back">
    <div class="brand-area"><div class="brand">Resinworks Hub</div></div>
    <div class="divider"></div>
    <div class="contact">
      <h1 class="person-name"><strong>Ted</strong> Galloway</h1>
      <p class="person-role">Founder &amp; CEO</p>
      <ul class="contact-list">
        <li>
          <svg viewBox="0 0 24 24" fill="#fff" aria-hidden="true"><path d="M6.6 10.8a15 15 0 0 0 6.6 6.6l2.2-2.2c.3-.3.7-.4 1-.2 1.1.4 2.3.6 3.6.6.6 0 1 .4 1 1V20c0 .6-.4 1-1 1A17 17 0 0 1 3 4c0-.6.4-1 1-1h3.5c.6 0 1 .4 1 1 0 1.3.2 2.5.6 3.6.1.3 0 .7-.2 1z"/></svg>
          604-712-3390
        </li>
        <li>
          <svg viewBox="0 0 24 24" fill="none" stroke="#fff" stroke-width="2" aria-hidden="true"><rect x="6" y="2" width="12" height="20" rx="2"/><line x1="11" y1="18" x2="13" y2="18"/></svg>
          604-947-2164
        </li>
        <li>
          <svg viewBox="0 0 24 24" fill="none" stroke="#fff" stroke-width="2" aria-hidden="true"><circle cx="12" cy="12" r="10"/><path d="M2 12h20M12 2a15 15 0 0 1 0 20M12 2a15 15 0 0 0 0 20"/></svg>
          www.resinworkshub.ca
        </li>
        <li>
          <svg viewBox="0 0 24 24" fill="none" stroke="#fff" stroke-width="2" aria-hidden="true"><rect x="2" y="5" width="20" height="14" rx="1"/><path d="M2 6l10 7 10-7"/></svg>
          ted@resinworkshub.ca
        </li>
      </ul>
    </div>
    <p class="address">7-4812 Fernhollow Road, Abbotsford, BC, V3K 8R2.</p>
  </section>
</main>
</body>
</html>
```